Maple Roster Business Card for recruitment company

We are looking for a Business Card Design that incorporates our personal details and our busines name and logo. We are a specialized search consultancy that recruit Property and Construction professionals.
We would like a business card that stands out and is appealing to the Construction and Property industry as well.

Target Market(s)

people in the construction and property industry

Contact Information for Business Card

Business Name and logo

Font styles to use
Serif

Colors
0094D4
00A9DD
6FCCEA
C7EBF8
E9F6FB

Requirements
Must have
• Business name and logo as well as contact details
Should not have
• No photos of us please

```html
<!DOCTYPE html>
<html lang="en">
<head>
<meta charset="utf-8">
<title>Maple Roster Business Card</title>
<link href="https://fonts.googleapis.com/css2?family=Josefin+Sans:wght@300&family=Montserrat:wght@400;600&display=swap" rel="stylesheet">
<style>
  :root {
    --page-bg: #d9d9d9;
    --card-teal: #013c4f;
    --accent-teal: #3ea6b2;
    --white: #ffffff;
  }
  * { margin: 0; padding: 0; box-sizing: border-box; }
  html, body { width: 800px; height: 1200px; overflow: hidden; }
  body {
    background: var(--page-bg);
    position: relative;
    font-family: "Montserrat", sans-serif;
    color: var(--white);
  }
  .card {
    position: absolute;
    left: 100px;
    width: 600px;
    height: 343px;
    background: var(--card-teal);
    overflow: hidden;
    box-shadow: 0 6px 18px rgba(0,0,0,0.35);
  }
  .card-front { top: 207px; }
  .card-back { top: 650px; }

  .brand-name {
    font-family: "Josefin Sans", sans-serif;
    font-weight: 300;
    color: var(--white);
    text-transform: uppercase;
    white-space: nowrap;
    line-height: 1;
  }
  .card-front .brand-name {
    position: absolute;
    top: 136px;
    left: 0;
    width: 100%;
    text-align: center;
    font-size: 50px;
    letter-spacing: 1px;
  }
  .front-url {
    position: absolute;
    top: 287px;
    width: 100%;
    text-align: center;
    font-weight: 600;
    font-size: 18px;
    letter-spacing: 1.5px;
  }
  .accent-bar {
    position: absolute;
    bottom: 0;
    left: 82px;
    width: 436px;
    height: 5px;
    background: var(--accent-teal);
    border-radius: 4px 4px 0 0;
  }

  .corner-panel { position: absolute; inset: 0; }
  .card-back .brand-name {
    position: absolute;
    top: 60px;
    left: 38px;
    font-size: 34px;
    letter-spacing: 0.5px;
  }
  .person-name {
    position: absolute;
    top: 120px;
    left: 38px;
    font-weight: 600;
    font-size: 21px;
    color: var(--accent-teal);
    letter-spacing: 0.5px;
    text-transform: uppercase;
  }
  .person-role {
    position: absolute;
    top: 148px;
    left: 38px;
    font-size: 12px;
    letter-spacing: 0.3px;
  }
  .contact-list {
    position: absolute;
    top: 206px;
    left: 38px;
    list-style: none;
  }
  .contact-item {
    display: flex;
    align-items: center;
    height: 27px;
    font-weight: 600;
    font-size: 16px;
    letter-spacing: 0.6px;
  }
  .contact-icon { width: 16px; height: 16px; margin-right: 12px; flex: none; }
</style>
</head>
<body>

<section class="card card-front">
  <div class="brand-name">Maple Roster</div>
  <div class="front-url">www.mapleroster.nz</div>
  <div class="accent-bar"></div>
</section>

<section class="card card-back">
  <svg class="corner-panel" width="600" height="343" viewBox="0 0 600 343" aria-hidden="true">
    <polygon points="600,0 600,343 333,343" fill="#ffffff"/>
  </svg>
  <div class="brand-name">Maple Roster</div>
  <div class="person-name">Clara Benning</div>
  <div class="person-role">Senior Search Consultant</div>
  <ul class="contact-list">
    <li class="contact-item">
      <svg class="contact-icon" viewBox="0 0 16 16" aria-hidden="true">
        <path d="M3.5 1.5l2.5 0.5 1 3-1.8 1.2a8 8 0 0 0 4.6 4.6L11 9l3 1 .5 2.5-2 1.8C7 14 2 9 1.7 3.5z" fill="none" stroke="#3ea6b2" stroke-width="1.4" stroke-linejoin="round"/>
      </svg>
      +64 27 555 0142
    </li>
    <li class="contact-item">
      <svg class="contact-icon" viewBox="0 0 16 16" aria-hidden="true">
        <rect x="1" y="3.5" width="14" height="9.5" fill="#3ea6b2"/>
        <path d="M1 3.5l7 5.5 7-5.5M1 13l5-4.5M15 13l-5-4.5" fill="none" stroke="#013c4f" stroke-width="1.1"/>
      </svg>
      c.benning@mapleroster.nz
    </li>
    <li class="contact-item">
      <svg class="contact-icon" viewBox="0 0 16 16" aria-hidden="true">
        <g fill="none" stroke="#3ea6b2" stroke-width="1.2">
          <circle cx="8" cy="8" r="6.5"/>
          <ellipse cx="8" cy="8" rx="3" ry="6.5"/>
          <path d="M1.5 8h13M2.5 4.8h11M2.5 11.2h11M8 1.5v13"/>
        </g>
      </svg>
      www.mapleroster.nz
    </li>
  </ul>
</section>

</body>
</html>
```